Northfield Builders Guild Business card

We are looking for a new business card design with photo included.
Our business is a nonprofit construction contractor membership organization. We offer business education, assist with business setup and licensing, provide safety training, and provide a member directory.
URL: www.builderslinkguild.org
Color code:
CMYK: 0 cyan, 42 magenta, 100 yellow, 0 black for Print.
Hexidecimal: #FF9900
RGB: R 255; G 153; B 0

```html
<!DOCTYPE html>
<html lang="en">
<head>
<meta charset="utf-8">
<title>Northfield Builders Guild – Business Card</title>
<link href="https://fonts.googleapis.com/css2?family=Arimo:wght@400;700&display=swap" rel="stylesheet">
<style>
  :root {
    --backdrop: #e4e4e4;
    --card: #343434;
    --accent: #ff9900;
    --ink: #ffffff;
    --radius: 70px;
  }
  * { margin: 0; padding: 0; box-sizing: border-box; }
  html, body { width: 1200px; height: 900px; overflow: hidden; }
  body {
    background: var(--backdrop);
    font-family: "Arimo", Arial, sans-serif;
    color: var(--ink);
    position: relative;
  }
  .card {
    position: absolute;
    top: 217px;
    width: 309px;
    height: 501px;
    background: var(--card);
  }
  .card--front {
    left: 279px;
    border-radius: 0 var(--radius) 0 var(--radius);
  }
  .card--back {
    left: 617px;
    border-radius: var(--radius) 0 var(--radius) 0;
  }
  .brand-name {
    position: absolute;
    left: 0; right: 0;
    text-align: center;
    font-weight: 700;
    color: var(--ink);
    font-size: 26px;
    line-height: 1.05;
    letter-spacing: 0.5px;
    text-transform: uppercase;
  }
  .card--front .brand-name { top: 150px; }
  .card--back .brand-name { top: 104px; }

  .services {
    position: absolute;
    left: 32px;
    top: 318px;
    list-style: none;
    font-size: 13px;
    line-height: 19px;
  }
  .services li {
    position: relative;
    padding-left: 12px;
    margin-bottom: 13px;
  }
  .services li::before {
    content: "";
    position: absolute;
    left: 0; top: 6px;
    width: 6px; height: 6px;
    border-radius: 50%;
    background: var(--accent);
  }

  .contact {
    position: absolute;
    left: 32px;
    top: 266px;
  }
  .contact__name {
    color: var(--accent);
    font-weight: 700;
    font-size: 19px;
    line-height: 20px;
  }
  .contact__title {
    font-size: 13px;
    margin-top: 3px;
  }
  .contact__list {
    list-style: none;
    margin-top: 12px;
    font-size: 14.5px;
  }
  .contact__list li {
    display: flex;
    align-items: center;
    height: 19px;
  }
  .contact__icon {
    width: 17px; height: 17px;
    margin-right: 4px;
    flex: none;
  }
  .accent { color: var(--accent); }
  .contact__address {
    margin-top: 13px;
    font-size: 14.5px;
    line-height: 18px;
    font-style: normal;
  }
</style>
</head>
<body>

  <section class="card card--front" aria-label="Card front">
    <div class="brand-name">Northfield<br>Builders<br>Guild</div>
    <ul class="services">
      <li>BUSINESS EDUCATION</li>
      <li>ASSIST WITH BUSINESS SETUP<br>AND LICENSING</li>
      <li>PROVIDE SAFETY TRAINING</li>
      <li>PROVIDE A MEMBER DIRECTORY</li>
    </ul>
  </section>

  <section class="card card--back" aria-label="Card back">
    <div class="brand-name">Northfield<br>Builders<br>Guild</div>
    <div class="contact">
      <div class="contact__name">DANIEL PORTER</div>
      <div class="contact__title">MANAGING DIRECTOR</div>
      <ul class="contact__list">
        <li>
          <svg class="contact__icon" viewBox="0 0 20 20" aria-hidden="true">
            <circle cx="10" cy="10" r="10" fill="#ff9900"/>
            <path d="M6.5 5.5l2 0 1 2.5-1.3 1a6 6 0 0 0 2.8 2.8l1-1.3 2.5 1v2a1 1 0 0 1-1 1A8.5 8.5 0 0 1 5.5 6.5a1 1 0 0 1 1-1z" fill="#343434"/>
          </svg>
          (503) 555-0142&nbsp;<span class="accent">(Office)</span>
        </li>
        <li>
          <svg class="contact__icon" viewBox="0 0 20 20" aria-hidden="true">
            <circle cx="10" cy="10" r="10" fill="#ff9900"/>
            <rect x="6.5" y="4.5" width="7" height="11" rx="1.2" fill="#343434"/>
            <rect x="7.7" y="6" width="4.6" height="6.5" fill="#ff9900"/>
          </svg>
          800-555-0199
        </li>
        <li>
          <svg class="contact__icon" viewBox="0 0 20 20" aria-hidden="true">
            <circle cx="10" cy="10" r="10" fill="#ff9900"/>
            <rect x="7" y="4.5" width="6" height="3" fill="#343434"/>
            <rect x="5" y="8" width="10" height="5" rx="1" fill="#343434"/>
            <rect x="7" y="11" width="6" height="4.5" fill="#343434" stroke="#ff9900" stroke-width="0.8"/>
          </svg>
          503.555.0173
        </li>
        <li>
          <svg class="contact__icon" viewBox="0 0 20 20" aria-hidden="true">
            <circle cx="10" cy="10" r="10" fill="#ff9900"/>
            <rect x="5" y="6.5" width="10" height="7" fill="#343434"/>
            <path d="M5 6.5l5 4 5-4" fill="none" stroke="#ff9900" stroke-width="0.9"/>
          </svg>
          support@nbguild.org
        </li>
        <li>
          <svg class="contact__icon" viewBox="0 0 20 20" aria-hidden="true">
            <circle cx="10" cy="10" r="10" fill="#ff9900"/>
            <g fill="none" stroke="#343434" stroke-width="1">
              <circle cx="10" cy="10" r="5"/>
              <ellipse cx="10" cy="10" rx="2.2" ry="5"/>
              <path d="M5 10h10M6 7.5h8M6 12.5h8"/>
            </g>
          </svg>
          www.<span class="accent">builderslinkguild</span>.org
        </li>
      </ul>
      <address class="contact__address">
        2400 NE Alder Ave<br>
        Suite #200, Portland, OR 97232
      </address>
    </div>
  </section>

</body>
</html>
```